Business Cards for new orthopaedic surgery practice

My husband and I are starting our own orthopaedic surgery practice. We are looking for a business card that is uniform, but one will have my name/title and the other will have his. You can just create one design with my name on it for now. But when I choose your design as the winning design I will ask that you add another copy with his name/title.

We are looking for classy, simple, elite all in one. We like dark blues/a little gold/yellow. Something that goes with our logo. We want our logo incorporated. Here is all the info you need:
Business name: RV Bone & Vitality Center
Location: 38517 North Willowmere Ave
Coral Springs, FL 33071
Phone: 954-218-4063
Fax: 954-582-7341
Email: info@myrvbonecare.example

Names: Lydia Vance, M.D.
Board Certified Hand and Upper Extremity Surgeon

Ebo Dansu, M.D.
Board Certified Hip & Knee Replacement/General Orthopaedic Surgeon

Can decide what you want to put on the back. Maybe a slogan:
Strong Motion. Steady Lives

I am just going to upload our logo. The only thing is if we select you as the winning design, the location, and phone numbers may change. We will need your help to update that once fully solidified.

Industry/Entity Type

Medical

Contact Information for Business Card

Colors
0054AA
0677BA
7BADD7
CADEEF
E8F1F8
0094D4
00A9DD
6FCCEA
C7EBF8
E9F6FB

Requirements
Must have
• class, appeal,
Should not have
• We want to air on the side of masculine if we are looking at masculine vs. feminine feel. But we still want it classy, sophisticated, and something we will love

```html
<!DOCTYPE html>
<html lang="en">
<head>
<meta charset="UTF-8">
<title>RV Bone &amp; Vitality Center — Business Card</title>
<link href="https://fonts.googleapis.com/css2?family=Marcellus&family=Montserrat:wght@400;500;700&display=swap" rel="stylesheet">
<style>
  :root {
    --navy: #243d82;
    --cyan: #1cb7df;
    --white: #ffffff;
    --ink: #1c2340;
    --backdrop: #dcdcdc;
    --photo-dark: #2a2124;
    --photo-mid: #7a5443;
    --photo-light: #c99a7d;
  }
  * { box-sizing: border-box; margin: 0; padding: 0; }
  html, body { width: 1200px; height: 1016px; overflow: hidden; }
  body {
    position: relative;
    background: var(--backdrop);
    font-family: "Montserrat", Arial, sans-serif;
  }
  .card {
    position: absolute;
    left: 298px;
    width: 603px;
    height: 345px;
    overflow: hidden;
    box-shadow: 0 10px 22px rgba(0,0,0,0.18);
  }
  .card-front { top: 140px; background: var(--navy); }
  .card-back { top: 536px; background: var(--white); }

  .brand {
    display: flex;
    align-items: center;
    font-family: "Marcellus", Georgia, serif;
    font-weight: 400;
    text-transform: uppercase;
    letter-spacing: 0.5px;
    line-height: 1;
  }
  .brand-name span { display: block; }
  .brand-dot { border-radius: 50%; flex: none; }

  .card-front .brand {
    position: absolute;
    left: 0; right: 0; top: 120px;
    justify-content: center;
    gap: 22px;
    color: var(--white);
    font-size: 36px;
  }
  .card-front .brand-name span + span { margin-top: 2px; }
  .card-front .brand-dot { width: 58px; height: 58px; background: var(--cyan); }

  .tagline {
    position: absolute;
    left: 0; right: 0; top: 293px;
    text-align: center;
    color: var(--white);
    font-size: 14.5px;
    letter-spacing: 0.2px;
  }

  .card-back .brand {
    position: absolute;
    left: 24px; top: 56px;
    gap: 16px;
    color: var(--navy);
    font-size: 22px;
  }
  .card-back .brand-dot { width: 40px; height: 40px; background: var(--cyan); }

  .name-band {
    position: absolute;
    left: 0; top: 154px;
    width: 388px; height: 58px;
    background: var(--navy);
    color: var(--white);
    padding: 9px 0 0 24px;
  }
  .name-band .doctor-name { font-weight: 700; font-size: 16.5px; letter-spacing: 0.3px; }
  .name-band .doctor-title { font-size: 13px; margin-top: 4px; letter-spacing: 0.2px; }

  .contact-list {
    position: absolute;
    left: 23px; top: 233px;
    list-style: none;
    color: var(--ink);
    font-size: 13.5px;
  }
  .contact-list li { display: flex; align-items: center; gap: 6px; height: 21.6px; }
  .contact-list svg { width: 12px; height: 12px; fill: var(--navy); flex: none; }

  .portrait {
    position: absolute;
    left: 335px; top: 25px;
    width: 268px; height: 320px;
    background: linear-gradient(160deg, var(--photo-dark) 0%, var(--photo-mid) 40%, var(--photo-light) 55%, var(--photo-dark) 80%);
    border-radius: 120px 120px 0 0;
  }
</style>
</head>
<body>

<section class="card card-front">
  <div class="brand">
    <span class="brand-dot"></span>
    <p class="brand-name"><span>RV Bone &amp;</span><span>Vitality</span><span>Center</span></p>
  </div>
  <p class="tagline">Strong Motion. Steady Lives</p>
</section>

<section class="card card-back">
  <div class="brand">
    <span class="brand-dot"></span>
    <p class="brand-name"><span>RV Bone &amp;</span><span>Vitality</span><span>Center</span></p>
  </div>

  <div class="portrait" role="img" aria-label="Portrait photograph of the doctor in a dark blazer"></div>

  <div class="name-band">
    <p class="doctor-name">LYDIA VANCE, M.D.</p>
    <p class="doctor-title">Hand and Upper Extremity Surgery</p>
  </div>

  <ul class="contact-list">
    <li>
      <svg viewBox="0 0 12 12" aria-hidden="true"><path d="M1 4.5C1 2.5 3.5 1.5 6 1.5S11 2.5 11 4.5H8.5V3.5h-5v1zM2.5 5.5h7l1 5h-9z"/></svg>
      954-218-4063
    </li>
    <li>
      <svg viewBox="0 0 12 12" aria-hidden="true"><path d="M3 1h6v3H3zM1 4.5h10v4.5H9V7H3v2H1zM3.5 7.5h5v3.5h-5z"/></svg>
      954-582-7341
    </li>
    <li>
      <svg viewBox="0 0 12 12" aria-hidden="true"><path d="M1 2.5h10v.8L6 6.5 1 3.3zM1 4.4l5 3.2 5-3.2V9.5H1z"/></svg>
      info@myrvbonecare.example
    </li>
    <li>
      <svg viewBox="0 0 12 12" aria-hidden="true"><circle cx="6" cy="6" r="5"/><path d="M3 4.5l2 1-1 2 1.5 2M7.5 2.5l-.5 2 2 1.5" stroke="#fff" stroke-width="0.9" fill="none"/></svg>
      www.myrvbonecare.example
    </li>
  </ul>
</section>

</body>
</html>
```